Window and GutterCleaning Flyer A5 size double sided.

We need a double sided A5 flyer. Side 1, is for window cleaning, side 2 is for gutter cleaning. Licensed by Borough of Marlow Council.
Phone number 0800 473 1926.
Business address 17 Fallowmere Close, North Brack Edinburgh EH31 4LP.
www.clearpane-hub-services.com
We use a LoftEye Gutter inspection Cam to view your gutters first to see if they need doing.
Window cleaning ; Professional window cleaning services, what we offer, water fed pole window cleaning able to reach windows up to 60 feet.
Conservatory cleaning.
Conservatory roof cleaning.
Fascias & Soffits cleaning.
Excellent Customer Service.
Target Market(s)
domestic houses
Industry/Entity Type
window cleaning
Look and feel
Each slider illustrates characteristics of the customer's brand and the style your logo design should communicate.

```html
<!DOCTYPE html>
<html lang="en">
<head>
<meta charset="utf-8">
<title>ClearPane Hub – Window &amp; Gutter Cleaning Flyer</title>
<link href="https://fonts.googleapis.com/css2?family=Bebas+Neue&family=Poppins:wght@400;500;600;700;800&display=swap" rel="stylesheet">
<style>
:root{
  --navy:#2e2a6b;
  --navy-deep:#252159;
  --sky:#9ec9ec;
  --sky-soft:#c4def4;
  --red:#d81f26;
  --green:#3f7d2a;
  --white:#ffffff;
  --ink:#1f1f2e;
  --stage:#f6f6f6;
}
*{box-sizing:border-box;margin:0;padding:0}
html,body{width:1200px;height:812px;overflow:hidden;background:var(--stage)}
body{position:relative;font-family:"Poppins",sans-serif;color:var(--ink)}
.flyer{position:absolute;top:72px;width:471px;height:667px;background:var(--white);overflow:hidden;box-shadow:0 4px 14px rgba(0,0,0,.25)}
.flyer--windows{left:80px}
.flyer--gutters{left:649px}
.backdrop{position:absolute;inset:0;width:471px;height:667px}
.abs{position:absolute}
.photo-circle{position:absolute;border-radius:50%;border:3px solid var(--white)}
.brand{position:absolute;display:flex;align-items:center;gap:5px;background:var(--sky);padding:5px 7px}
.brand__mark{width:10px;height:10px;background:var(--navy)}
.brand__name{font-weight:800;font-size:11px;color:var(--navy);letter-spacing:.3px;line-height:1}
.offer-panel{position:absolute;background:var(--navy);border-radius:0 0 16px 16px}
.offer-band{position:absolute;background:var(--sky);display:flex;align-items:center;justify-content:center;font-weight:800;font-size:17px;color:var(--navy);letter-spacing:.2px}
.ticks{list-style:none;position:absolute;font-size:9px;line-height:1.2}
.ticks li{position:relative;padding-left:14px;margin-bottom:8px}
.ticks li::before{content:"";position:absolute;left:0;top:1px;width:9px;height:9px;border-radius:50%;background:var(--sky)}
.ticks li::after{content:"";position:absolute;left:3px;top:3px;width:2.5px;height:4px;border:solid var(--navy);border-width:0 1.3px 1.3px 0;transform:rotate(45deg)}
.ticks--light{color:var(--white)}
.ticks--dark{color:var(--ink);font-weight:500;font-size:9px}
.ticks--dark li{margin-bottom:5px}
.ticks--dark li::after{border-color:var(--white)}
.headline{position:absolute;font-weight:800;color:var(--ink);font-size:15.5px;line-height:.92;letter-spacing:-.2px;white-space:nowrap}
.tab{position:absolute;background:var(--navy);color:var(--white);font-weight:700;font-size:10.5px;letter-spacing:1px;padding:3px 8px;white-space:nowrap;clip-path:polygon(0 0,94% 0,100% 100%,0 100%)}
.tab--tight{letter-spacing:.3px;font-size:11px}
.slab{position:absolute;background:var(--sky);color:var(--navy);font-family:"Bebas Neue",sans-serif;line-height:1;padding:3px 8px;border-radius:3px;white-space:nowrap}
.body-copy{position:absolute;font-size:10.5px;line-height:1.13;color:var(--ink)}
.burst{position:absolute;background:var(--red);color:var(--white);font-weight:800;text-align:center;display:flex;align-items:center;justify-content:center;line-height:1.05;
  clip-path:polygon(100% 50%,92.2% 58.4%,96.2% 69.1%,85.7% 73.9%,85.4% 85.4%,73.9% 85.7%,69.1% 96.2%,58.4% 92.2%,50% 100%,41.6% 92.2%,30.9% 96.2%,26.1% 85.7%,14.6% 85.4%,14.3% 73.9%,3.8% 69.1%,7.8% 58.4%,0 50%,7.8% 41.6%,3.8% 30.9%,14.3% 26.1%,14.6% 14.6%,26.1% 14.3%,30.9% 3.8%,41.6% 7.8%,50% 0,58.4% 7.8%,69.1% 3.8%,73.9% 14.3%,85.4% 14.6%,85.7% 26.1%,96.2% 30.9%,92.2% 41.6%)}
.display{position:absolute;font-family:"Bebas Neue",sans-serif;color:var(--navy);line-height:.9}
.contact{position:absolute;display:flex;align-items:center;gap:4px;color:var(--navy);font-weight:600;white-space:nowrap}
.contact svg{flex:none}
.web{position:absolute;font-weight:700;font-size:13px;color:var(--ink);letter-spacing:.1px;white-space:nowrap}
.circle-label{position:absolute;font-weight:700;font-size:10px;color:var(--navy);text-align:center}
.arrow-label{position:absolute;font-weight:700;color:var(--white);font-size:23px;text-align:center;line-height:1}
.red-title{position:absolute;font-family:"Bebas Neue",sans-serif;color:var(--red);font-size:19px;line-height:1;white-space:nowrap}
.why{position:absolute;font-weight:800;font-size:17px;color:var(--navy);white-space:nowrap}
.small-bold{position:absolute;font-weight:700;font-size:9px;line-height:1.15;color:var(--navy)}
</style>
</head>
<body>

<!-- Side 1: window cleaning -->
<section class="flyer flyer--windows">
  <svg class="backdrop" viewBox="0 0 471 667" aria-hidden="true">
    <defs>
      <linearGradient id="ropeSky" x1="0" y1="0" x2="1" y2="1">
        <stop offset="0" stop-color="#9fb3c9"/>
        <stop offset=".55" stop-color="#6c7180"/>
        <stop offset="1" stop-color="#3a3c48"/>
      </linearGradient>
    </defs>
    <rect x="0" y="0" width="471" height="330" fill="url(#ropeSky)"/>
    <path d="M0,255 Q90,305 220,270 T471,228 L471,667 L0,667Z" fill="var(--navy)"/>
    <path d="M0,263 Q90,310 220,277 T471,238 L471,667 L0,667Z" fill="var(--white)"/>
    <path d="M0,520 Q120,500 250,545 T471,515 L471,667 L0,667Z" fill="var(--navy)"/>
    <path d="M0,532 Q120,512 250,560 T471,530 L471,667 L0,667Z" fill="var(--sky)"/>
  </svg>
  <div class="abs" role="img" aria-label="Rope-access window cleaner washing a tall building facade" style="left:0;top:0;width:300px;height:250px"></div>

  <div class="offer-panel" style="left:258px;top:237px;width:190px;height:251px"></div>

  <div class="photo-circle" role="img" aria-label="Photo of a white conservatory" style="left:263px;top:163px;width:98px;height:98px;background:linear-gradient(160deg,#cfe0ef,#a99a88)"></div>
  <div class="photo-circle" role="img" aria-label="Photo of a cleaner with a water-fed pole at a house" style="left:347px;top:160px;width:104px;height:104px;background:linear-gradient(160deg,#b58d76,#6e5a4c)"></div>

  <div class="brand" style="left:312px;top:95px">
    <span class="brand__mark"></span><span class="brand__name">CLEARPANE HUB</span>
  </div>

  <div class="offer-band" style="left:250px;top:296px;width:204px;height:29px">WE OFFER</div>
  <ul class="ticks ticks--light" style="left:276px;top:338px;width:165px">
    <li>Water-Fed Pole Cleaning<br>Up to 60 Feet</li>
    <li>Conservatory Windows &amp; Roofs</li>
    <li>Fascia &amp; Soffit Cleaning</li>
    <li>One-off or Regular Cleans</li>
    <li>Reliable, Friendly Service</li>
    <li>Licensed by Borough of<br>Marlow Council</li>
  </ul>

  <h1 class="headline" style="left:41px;top:312px">LET THE SUNSHINE IN<br>SPARKLING WINDOWS<br>GUARANTEED!</h1>
  <div class="tab" style="left:40px;top:362px;width:180px">WE OFFER HIGH-QUALITY</div>
  <div class="slab" style="left:40px;top:383px;font-size:31px">WINDOW CLEANING</div>
  <p class="body-copy" style="left:41px;top:424px;width:200px">for homes and businesses, delivering. We only clean domestic properties not businesses. Spotless, streak-free results every time. As per last info, can't claim this too.</p>

  <div class="photo-circle" role="img" aria-label="Before photo of a mossy gutter" style="left:118px;top:497px;width:65px;height:65px;background:linear-gradient(180deg,#e3ecf5 0 30%,#8a7f57 30%)"></div>
  <div class="circle-label" style="left:118px;top:500px;width:65px">Before</div>
  <div class="photo-circle" role="img" aria-label="After photo of a clean white fascia" style="left:190px;top:510px;width:84px;height:84px;background:linear-gradient(180deg,#e3ecf5 0 22%,#d8dde3 22%,#b9c0c8)"></div>
  <div class="circle-label" style="left:190px;top:513px;width:84px">After</div>

  <div class="burst" style="left:286px;top:480px;width:136px;height:136px;font-size:9.5px;padding:0 10px">"GREAT SERVICE<br>FROM START TO<br>FINISH. RELIABLE,<br>PROFESSIONAL AND<br>THE WINDOWS HAVE<br>NEVER LOOKED<br>BETTER!"</div>

  <div class="display" style="left:41px;top:538px;font-size:22px">BASED IN<br>NORTH BRACK</div>
  <div class="abs" style="left:41px;top:577px;font-weight:700;font-size:12px;color:var(--white);white-space:nowrap">Serving All of Edinburgh</div>
  <div class="contact" style="left:41px;top:596px;font-size:12px">
    <svg width="8" height="8" viewBox="0 0 10 10"><circle cx="5" cy="5" r="5" fill="var(--navy)"/><path d="M3 2.6l1 .1.4 1.2-.6.5a3.5 3.5 0 0 0 1.8 1.8l.5-.6 1.2.4.1 1c-2.4.4-4.8-2-4.4-4.4z" fill="var(--sky)"/></svg>
    0800 473 1926
  </div>
  <div class="contact" style="left:41px;top:613px;font-size:8.5px;align-items:flex-start;line-height:1.2">
    <svg width="8" height="8" viewBox="0 0 10 10" style="margin-top:1px"><circle cx="5" cy="5" r="5" fill="var(--navy)"/><circle cx="5" cy="4.3" r="1.5" fill="var(--sky)"/></svg>
    <span>17 Fallowmere Close, North<br>Brack, Edinburgh EH31 4LP</span>
  </div>
  <div class="web" style="left:205px;top:622px">www.clearpane-hub-services.com</div>
</section>

<!-- Side 2: gutter cleaning -->
<section class="flyer flyer--gutters">
  <svg class="backdrop" viewBox="0 0 471 667" aria-hidden="true">
    <defs>
      <linearGradient id="eaves" x1="0" y1="0" x2="1" y2="1">
        <stop offset="0" stop-color="#ffffff"/>
        <stop offset=".45" stop-color="#e8ecef"/>
        <stop offset=".75" stop-color="#7b7e84"/>
        <stop offset="1" stop-color="#8b5a48"/>
      </linearGradient>
    </defs>
    <rect x="0" y="0" width="471" height="330" fill="url(#eaves)"/>
    <path d="M0,255 Q90,305 220,270 T471,228 L471,667 L0,667Z" fill="var(--navy)"/>
    <path d="M0,263 Q90,310 220,277 T471,238 L471,667 L0,667Z" fill="var(--white)"/>
    <path d="M0,505 Q120,485 250,535 T471,525 L471,667 L0,667Z" fill="var(--navy)"/>
    <path d="M0,517 Q120,497 250,550 T471,540 L471,667 L0,667Z" fill="var(--sky)"/>
    <path d="M190,21 L310,21 L310,13 L339,49 L310,85 L310,77 L190,77 L205,49Z" fill="var(--green)"/>
    <path d="M143,98 L264,98 L264,90 L293,126 L264,162 L264,154 L143,154 L158,126Z" fill="var(--green)"/>
    <path d="M97,186 L217,186 L217,178 L246,211 L217,244 L217,237 L97,237 L112,211Z" fill="var(--green)"/>
  </svg>
  <div class="abs" role="img" aria-label="Photo of a roofline gutter, fascia and soffit" style="left:170px;top:0;width:301px;height:240px"></div>
  <div class="arrow-label" style="left:205px;top:36px;width:110px">Gutter</div>
  <div class="arrow-label" style="left:158px;top:114px;width:110px">Fascia</div>
  <div class="arrow-label" style="left:112px;top:199px;width:110px">Soffit</div>

  <div class="offer-panel" style="left:258px;top:237px;width:190px;height:173px"></div>

  <div class="photo-circle" role="img" aria-label="Photo of a vacuum hose clearing a gutter" style="left:262px;top:163px;width:98px;height:98px;background:linear-gradient(160deg,#5a6cb0,#8e8a80)"></div>
  <div class="photo-circle" role="img" aria-label="Photo of a gutter vacuum pole against a garden" style="left:347px;top:160px;width:104px;height:104px;background:linear-gradient(160deg,#8fb06a,#5c6a4c)"></div>

  <div class="brand" style="left:30px;top:96px">
    <span class="brand__mark"></span><span class="brand__name">CLEARPANE HUB</span>
  </div>

  <div class="offer-band" style="left:250px;top:273px;width:204px;height:31px">WE OFFER</div>
  <ul class="ticks ticks--light" style="left:276px;top:316px;width:165px">
    <li>Safe, No-Ladder Cleaning</li>
    <li>Removes Moss, Leaves &amp; Debris</li>
    <li>Prevents Overflow, Damp &amp;<br>Water Damage</li>
    <li>Fast, Clean &amp; Fully Insured</li>
  </ul>

  <h2 class="headline" style="left:29px;top:303px">DON'T LET BLOCKED<br>GUTTERS CAUSE<br>COSTLY DAMAGE</h2>
  <div class="tab tab--tight" style="left:29px;top:353px;width:192px">WE INSPECT BEFORE WE CLEAN</div>
  <div class="slab" style="left:29px;top:374px;font-size:22px;padding:2px 6px">SAVING YOU TIME AND MONEY</div>

  <div class="abs" role="img" aria-label="Inspection camera tablet showing a house" style="left:30px;top:421px;width:85px;height:62px;border-radius:6px;background:linear-gradient(150deg,#3c3f46,#1d1f24);border:2px solid #e07a1f"></div>
  <div class="red-title" style="left:126px;top:419px">FREE GUTTER CHECK</div>
  <p class="body-copy" style="left:126px;top:440px;width:125px;font-size:9.5px;font-weight:500">with LoftEye Inspection Cam We show you what's really going on before recommending service.</p>

  <div class="why" style="left:275px;top:421px">WHY CHOOSE US?</div>
  <ul class="ticks ticks--dark" style="left:275px;top:444px;width:175px">
    <li>Safe, No-Ladder Cleaning</li>
    <li>Removes Moss, Leaves &amp; Debris</li>
    <li>Prevents Overflow, Damp &amp;<br>Water Damage</li>
    <li>Fast, Clean &amp; Fully Insured</li>
  </ul>

  <div class="photo-circle" role="img" aria-label="Photo of a customer service agent with a headset" style="left:167px;top:497px;width:110px;height:110px;background:linear-gradient(160deg,#d9dde3,#a7b4c2)"></div>

  <div class="burst" style="left:309px;top:516px;width:98px;height:98px;font-size:8.5px;padding:0 12px">STAY<br>AHEAD OF<br>LEAKS BOOK<br>YOUR GUTTER<br>CHECK<br>TODAY!</div>

  <div class="display" style="left:29px;top:534px;font-size:27px">GET A<br>FREE QUOTE</div>
  <div class="contact" style="left:29px;top:586px;font-size:15px">
    <svg width="10" height="10" viewBox="0 0 10 10"><circle cx="5" cy="5" r="5" fill="var(--navy)"/><path d="M3 2.6l1 .1.4 1.2-.6.5a3.5 3.5 0 0 0 1.8 1.8l.5-.6 1.2.4.1 1c-2.4.4-4.8-2-4.4-4.4z" fill="var(--sky)"/></svg>
    0800 473 1926
  </div>
  <div class="small-bold" style="left:29px;top:606px;width:160px">Licensed by Borough of Marlow Council Professional.<br>Affordable. Local.</div>
  <div class="web" style="left:204px;top:620px">www.clearpane-hub-services.com</div>
</section>

</body>
</html>
```